Poster

I need a poster for my business, www.coastalsupperroutesnerja.example which some information about the most important activities (Sangria Tasting, Iberian Ham, Charcuteries & Sherry Wine Tasting, Sailboat Experiences and Picnic Experiences). A3 Format. Social media included (@coastalsupperroutescsr), contact information included.

```html
<!DOCTYPE html>
<html lang="en">
<head>
<meta charset="utf-8">
<title>Coastal Supper Routes – Poster</title>
<link rel="stylesheet" href="https://fonts.googleapis.com/css2?family=Montserrat:wght@800&family=Oswald:wght@400;500&family=Poppins:wght@400;500;600;700&family=Yellowtail&display=swap">
<style>
:root{
  --purple:#5a1f8c;
  --orange:#f5a11a;
  --red:#e31e2a;
  --ink:#1c1c1c;
  --white:#ffffff;
  --line:#3a3a3a;
  --night:#2a1a14;
}
*{margin:0;padding:0;box-sizing:border-box}
html,body{width:854px;height:1200px;overflow:hidden;background:var(--white)}
.poster{position:relative;width:854px;height:1200px;overflow:hidden;font-family:"Poppins",sans-serif;color:var(--ink);background:var(--white)}
.hero{position:absolute;left:0;top:0;width:854px;height:560px;background:linear-gradient(180deg,#5b2291 0%,#54208a 28%,#4a2473 38%,#6b4a6e 50%)}
.hero-photo{position:absolute;left:0;top:250px;width:854px;height:310px;background:radial-gradient(ellipse at 60% 45%,#b88a4e 0%,#6e4a45 35%,#3b2a2c 70%,#221614 100%)}
.hero-fade{position:absolute;left:0;top:230px;width:854px;height:80px;background:linear-gradient(180deg,#4f2380 0%,rgba(79,35,128,0) 100%)}
.brand{position:absolute;left:62px;top:128px;display:flex;align-items:center;gap:14px}
.brand-mark{width:24px;height:24px;background:var(--orange)}
.brand-name{font-family:"Oswald",sans-serif;font-weight:500;font-size:30px;line-height:1.05;color:var(--white);letter-spacing:.5px;text-transform:uppercase}
.kicker{position:absolute;left:342px;top:40px;font-family:"Yellowtail",cursive;font-size:96px;line-height:1;color:var(--orange);transform:rotate(-6deg);transform-origin:left center}
.headline{position:absolute;left:334px;top:136px;font-family:"Montserrat",sans-serif;font-weight:800;font-size:69px;line-height:58px;color:var(--white);letter-spacing:-.5px}
.tear{position:absolute;left:0;width:854px}
.tear-top{top:500px;height:90px}
.tear-bottom{top:990px;height:210px}
.contact{position:absolute;left:0;top:1040px;width:854px;height:160px}
.contact-title{position:absolute;left:71px;top:12px;font-weight:700;font-size:25px;color:var(--ink)}
.contact-item{position:absolute;top:54px}
.contact-label{font-size:15.5px;font-weight:400;color:var(--ink);white-space:nowrap}
.contact-value{display:flex;align-items:center;gap:7px;margin-top:8px;white-space:nowrap}
.contact-value svg{flex:none}
.contact-value.is-phone{font-weight:700;font-size:19px}
.contact-value.is-link{font-size:12.5px;font-weight:500}
.card{position:absolute;top:598px;width:179px;height:222px;border:1.2px solid var(--line);border-radius:12px;background:var(--white)}
.card-photo{position:absolute;left:5px;top:6px;width:167px;height:156px;border-radius:8px}
.card-title{position:absolute;left:0;right:0;top:168px;height:42px;display:flex;align-items:center;justify-content:center;text-align:center;font-family:"Oswald",sans-serif;font-weight:400;font-size:14px;line-height:17px;color:var(--ink)}
.book{position:absolute;left:50%;bottom:-14px;transform:translateX(-50%);width:80px;height:21px;border-radius:11px;background:var(--orange);color:var(--white);font-size:10px;display:flex;align-items:center;justify-content:center}
.badge{position:absolute;left:50%;top:-34px;transform:translateX(-50%);width:58px;height:66px}
.badge svg{position:absolute;inset:0}
.badge-label{position:absolute;left:0;right:0;top:18px;text-align:center;color:var(--white);font-weight:600;font-size:8px}
.badge-time{position:absolute;left:6px;right:6px;top:30px;height:12px;border-radius:6px;background:var(--ink);color:var(--white);font-weight:600;font-size:8px;line-height:12px;text-align:center}
.info{position:absolute;top:846px;font-size:6.6px;line-height:8.2px;color:var(--ink)}
.tag{display:inline-block;border:1px solid var(--orange);border-radius:8px;padding:0 7px;font-size:8px;font-weight:600;line-height:11px;margin-bottom:4px;text-transform:uppercase}
.info p{margin-bottom:3px}
.info ul{list-style:none;margin-bottom:5px}
.info li{position:relative;padding-left:9px;margin-bottom:3px}
.info li::before{content:"";position:absolute;left:1px;top:2px;width:4px;height:4px;border-radius:50%;background:var(--ink)}
.info .strong{font-weight:700}
.info em{font-style:italic}
.twocol{display:grid;grid-template-columns:1fr 1fr;column-gap:6px}
</style>
</head>
<body>
<main class="poster">

  <header class="hero">
    <div class="hero-photo" role="img" aria-label="Night view of whitewashed hillside apartments above the sea, lit with warm lights"></div>
    <div class="hero-fade"></div>
    <div class="brand">
      <span class="brand-mark"></span>
      <span class="brand-name">Coastal Supper<br>Routes</span>
    </div>
    <div class="kicker">Enjoy</div>
    <h1 class="headline">MARBELLA &amp;<br>ESTEPONA</h1>
  </header>

  <svg class="tear tear-top" viewBox="0 0 854 90" preserveAspectRatio="none" aria-hidden="true">
    <polygon fill="var(--night)" points="0,40 854,40 854,90 0,90"/>
    <polygon fill="var(--white)" points="0,46 30,42 60,47 100,41 140,44 180,36 220,33 250,38 280,50 320,60 350,66 380,58 420,48 470,40 520,30 560,22 585,14 610,24 640,30 690,38 730,32 770,40 810,46 854,44 854,90 0,90"/>
  </svg>

  <article class="card" style="left:74px">
    <div class="badge"><svg viewBox="0 0 58 66"><polygon fill="var(--red)" points="29,0 58,16 58,50 29,66 0,50 0,16"/></svg><div class="badge-label">DURATION:</div><div class="badge-time">1H 30MIN</div></div>
    <div class="card-photo" role="img" aria-label="Friends sharing glasses of red sangria at a table" style="background:linear-gradient(135deg,#d9d3cc,#8a6a5a 55%,#6a1a24)"></div>
    <h2 class="card-title">Sangria Tasting</h2>
    <span class="book">Book now</span>
  </article>

  <article class="card" style="left:257px">
    <div class="badge"><svg viewBox="0 0 58 66"><polygon fill="var(--red)" points="29,0 58,16 58,50 29,66 0,50 0,16"/></svg><div class="badge-label">DURATION:</div><div class="badge-time">1H 30MIN</div></div>
    <div class="card-photo" role="img" aria-label="Bowl of green olives and a board of sliced Iberian ham" style="background:linear-gradient(160deg,#8a6a52,#3a2a22 50%,#1e1614)"></div>
    <h2 class="card-title">Iberian Ham Charcuteries<br>&amp; Sherry Wine Tasting</h2>
    <span class="book">Book now</span>
  </article>

  <article class="card" style="left:440px">
    <div class="badge"><svg viewBox="0 0 58 66"><polygon fill="var(--red)" points="29,0 58,16 58,50 29,66 0,50 0,16"/></svg><div class="badge-label">DURATION:</div><div class="badge-time">2H</div></div>
    <div class="card-photo" role="img" aria-label="Sailboat on open sea under a cloudy sunset sky" style="background:linear-gradient(180deg,#7f93ad 0%,#c7c0b0 45%,#35506e 70%,#1f3550 100%)"></div>
    <h2 class="card-title">Sailboat<br>Experiences</h2>
    <span class="book">Book now</span>
  </article>

  <article class="card" style="left:623px">
    <div class="badge"><svg viewBox="0 0 58 66"><polygon fill="var(--red)" points="29,0 58,16 58,50 29,66 0,50 0,16"/></svg><div class="badge-label">DURATION:</div><div class="badge-time">2H</div></div>
    <div class="card-photo" role="img" aria-label="Picnic basket with bread and wine on a striped blanket by the sea" style="background:linear-gradient(180deg,#e6e3df 0%,#9aa6b0 40%,#c9c4c0 70%,#8a5a3a 100%)"></div>
    <h2 class="card-title">Picnic<br>Experiences</h2>
    <span class="book">Book now</span>
  </article>

  <section class="info" style="left:81px;width:168px">
    <span class="tag">Inclusions</span>
    <p>Sampling of 4 types unique and delightful variations of classic Spanish Sangria:</p>
    <ul class="twocol">
      <li>Sherry Wine Sangria,</li><li>Sherry Wine Sangria,</li>
      <li>White Wine Sangria,</li><li>White Wine Sangria,</li>
    </ul>
    <span class="tag">Things to know about</span>
    <p>If you have any special dietary restrictions, please contact us before booking.</p>
    <p class="strong">Please arrive 15 minutes early</p>
  </section>

  <section class="info" style="left:280px;width:154px">
    <span class="tag">Inclusions</span>
    <ul>
      <li>Tasting of 2 Iberian hams<br>and 3 Iberian sausages</li>
      <li>Olives</li>
      <li>Sherry wine</li>
    </ul>
    <span class="tag">Things to know about</span>
    <p>If you have any specific dietary restrictions, please contact us before booking</p>
    <p class="strong">Please arrive 15 minutes early</p>
  </section>

  <section class="info" style="left:449px;width:170px">
    <span class="tag">Inclusions</span>
    <div class="twocol">
      <ul>
        <li>Smooth and tranquil sail</li>
        <li>A tasting of premium wines</li>
        <li>Selection of gourmet cheeses and accompaniments</li>
      </ul>
      <ul>
        <li>Expert guide sharing insights on wine and cheese pairing</li>
        <li>Stunning panoramic views of the Estepona coast</li>
      </ul>
    </div>
    <span class="tag">Things to know about</span>
    <p>Comfortable clothing and a light jacket for the sea breeze are recommended</p>
    <p><em>Note that in case of adverse weather, the schedule may be adjusted<br>Please arrive 15 minutes early</em></p>
    <p class="strong">Available slots at 17.30 and Sunset at 20.30 (subject to the sunset time)</p>
  </section>

  <section class="info" style="left:633px;width:170px">
    <span class="tag">Inclusions</span>
    <ul>
      <li>Choice of gourmet picnic basket filled with artisanal cheeses, freshly baked bread, cured meats, olives, seasonal fruits, and decadent desserts</li>
      <li>Bottle of premium Spanish wine or refreshing beverages</li>
      <li>Picnic blanket and utensils</li>
    </ul>
    <span class="tag">Things to know about</span>
    <p>If you have any special dietary restrictions, please contact us before booking.</p>
    <p>Please arrive 15 minutes early</p>
  </section>

  <svg class="tear tear-bottom" viewBox="0 0 854 210" preserveAspectRatio="none" aria-hidden="true">
    <polygon fill="var(--orange)" points="0,45 40,42 70,30 110,32 150,30 200,22 230,14 254,4 275,8 300,16 330,22 360,26 394,29 430,40 470,66 530,72 590,70 630,56 660,50 720,46 780,42 820,40 854,38 854,210 0,210"/>
  </svg>

  <footer class="contact">
    <h2 class="contact-title">Contact us!</h2>
    <div class="contact-item" style="left:71px">
      <div class="contact-label">Contact via WhatsApp</div>
      <div class="contact-value is-phone">
        <svg width="24" height="24" viewBox="0 0 24 24" aria-hidden="true"><circle cx="12" cy="12" r="12" fill="var(--ink)"/><path fill="var(--orange)" d="M8.6 6.5l1.6-.2 1 2.6-1 1c.6 1.3 1.6 2.3 2.9 2.9l1-1 2.6 1-.2 1.6c-.2.6-.8 1-1.4 1-4 0-7.5-3.5-7.5-7.5 0-.6.4-1.2 1-1.4z"/></svg>
        0034 600 123 456
      </div>
    </div>
    <div class="contact-item" style="left:312px">
      <div class="contact-label">Contact via email</div>
      <div class="contact-value is-link">
        <svg width="18" height="18" viewBox="0 0 18 18" aria-hidden="true"><circle cx="9" cy="9" r="9" fill="var(--ink)"/><rect x="4.5" y="5.8" width="9" height="6.4" rx="1" fill="none" stroke="var(--orange)" stroke-width="1.1"/><path d="M4.8 6.2L9 9.4l4.2-3.2" fill="none" stroke="var(--orange)" stroke-width="1.1"/></svg>
        @coastalsupperroutescsr
      </div>
    </div>
    <div class="contact-item" style="left:534px">
      <div class="contact-label">Visit our website</div>
      <div class="contact-value is-link">
        <svg width="18" height="18" viewBox="0 0 18 18" aria-hidden="true"><circle cx="9" cy="9" r="8" fill="none" stroke="var(--ink)" stroke-width="1.4"/><ellipse cx="9" cy="9" rx="3.4" ry="8" fill="none" stroke="var(--ink)" stroke-width="1.1"/><path d="M1 9h16M2.5 5h13M2.5 13h13" stroke="var(--ink)" stroke-width="1"/></svg>
        www.coastalsupperroutesnerja.example
      </div>
    </div>
  </footer>

</main>
</body>
</html>
```